Web Developer Needs a Business Card Design

I need a personal business card design that represents me as a web developer for potential employers. I would like the background to be a dark color on the front for contrast with my logo and name. The back will have all my information along with a smaller version of the logo. I want something with a modern look and feel, not too conservative. This will be used for potential employers and freelance work.

Industry/Entity Type

Business

Contact Information for Business Card

Front should have my logo and name. The back should have all my personal information which would include: name: Tom Varulek, phone: 570-614-3098, email: tomvarulek@quillbox.net, website url: www.tomvarulek.net, logo, web developer.

Font styles to use
Sans Serif

Requirements
Must have
• Must include my logo. The color palette base color will be the logo color.

```html
<!DOCTYPE html>
<html lang="en">
<head>
<meta charset="utf-8">
<title>Tom Varulek — Business Card</title>
<link rel="stylesheet" href="https://fonts.googleapis.com/css2?family=Open+Sans:wght@400;600;700&display=swap">
<style>
  :root {
    --stage: #1c1c1c;
    --card: #0e0e0e;
    --card-edge: #161616;
    --teal: #7fd3c0;
    --white: #f2f2f2;
    --muted: #d8d8d8;
  }
  * { margin: 0; padding: 0; box-sizing: border-box; }
  html, body {
    width: 1200px; height: 864px; overflow: hidden;
    background: var(--stage);
    font-family: "Open Sans", sans-serif;
  }
  .stage {
    width: 1200px; height: 864px;
    display: flex; align-items: center; justify-content: center; gap: 60px;
  }
  .card {
    position: relative;
    width: 500px; height: 286px;
    background: linear-gradient(135deg, var(--card-edge), var(--card) 60%);
    border-radius: 4px;
    overflow: hidden;
  }
  /* back (information side) */
  .tab {
    position: absolute; height: 11px; background: var(--teal);
  }
  .tab--top { top: 0; left: 236px; width: 136px; border-radius: 0 0 8px 8px; }
  .tab--bottom { bottom: 0; left: 148px; width: 150px; border-radius: 8px 8px 0 0; }
  .divider {
    position: absolute; left: 262px; top: 50px; width: 1px; height: 186px;
    background: var(--teal);
  }
  .contact { position: absolute; left: 46px; top: 82px; }
  .contact__name { color: var(--teal); font-weight: 700; font-size: 16px; line-height: 1.2; }
  .contact__role { color: var(--white); font-size: 12px; margin-bottom: 14px; }
  .contact__list { list-style: none; }
  .contact__item {
    display: flex; align-items: center; gap: 10px;
    color: var(--muted); font-size: 12px; line-height: 19px;
  }
  .contact__icon {
    width: 13px; height: 13px; border-radius: 2px; background: var(--teal);
    display: flex; align-items: center; justify-content: center;
  }
  .identity {
    position: absolute; display: flex; flex-direction: column; align-items: center; gap: 10px;
  }
  .identity--small { left: 262px; right: 0; top: 92px; }
  .identity--large { left: 0; right: 0; top: 92px; }
  .identity__mark {
    width: 48px; height: 48px; border-radius: 50%; border: 4px solid var(--teal);
  }
  .identity__name { color: var(--white); font-size: 22px; font-weight: 400; letter-spacing: 0.5px; }
</style>
</head>
<body>
<main class="stage">
  <section class="card card--back" aria-label="Card back with contact details">
    <span class="tab tab--top"></span>
    <span class="tab tab--bottom"></span>
    <div class="contact">
      <p class="contact__name">Tom Varulek</p>
      <p class="contact__role">Web Developer</p>
      <ul class="contact__list">
        <li class="contact__item">
          <span class="contact__icon">
            <svg width="9" height="9" viewBox="0 0 10 10"><path d="M2 1l2 2-1 1.2c.6 1.2 1.5 2.1 2.8 2.8L7 6l2 2-1.2 1.4C4.5 9 1 5.5.6 2.2z" fill="#0e0e0e"/></svg>
          </span>570-614-3098
        </li>
        <li class="contact__item">
          <span class="contact__icon">
            <svg width="9" height="9" viewBox="0 0 10 10"><rect x="0.5" y="2" width="9" height="6" fill="none" stroke="#0e0e0e" stroke-width="1.2"/><path d="M.5 2l4.5 3.5L9.5 2" fill="none" stroke="#0e0e0e" stroke-width="1.2"/></svg>
          </span>tomvarulek@quillbox.net
        </li>
        <li class="contact__item">
          <span class="contact__icon">
            <svg width="9" height="9" viewBox="0 0 10 10"><circle cx="5" cy="5" r="4.2" fill="none" stroke="#0e0e0e" stroke-width="1.1"/><ellipse cx="5" cy="5" rx="1.8" ry="4.2" fill="none" stroke="#0e0e0e" stroke-width="1"/><path d="M1 5h8" stroke="#0e0e0e" stroke-width="1"/></svg>
          </span>www.tomvarulek.net
        </li>
      </ul>
    </div>
    <span class="divider"></span>
    <div class="identity identity--small">
      <span class="identity__mark"></span>
      <p class="identity__name">TOM VARULEK</p>
    </div>
  </section>

  <section class="card card--front" aria-label="Card front with name">
    <div class="identity identity--large">
      <span class="identity__mark"></span>
      <p class="identity__name">TOM VARULEK</p>
    </div>
  </section>
</main>
</body>
</html>
```